Sierra Lantern Roots Festival Music Conference & Concert Series needs a banner design to welco...

We are looking for a banner to use as a backdrop where people can take pictures and promote the event as they upload to social media. The music conference primarily targets high school students so we are looking for a design that will attract a younger audience. The festival revolves around music appreciation in the US/Mexico border. We like the "Sierra LanternRoots Festival" trumpet logo on the "5th annual" design attached, but we are open to other designs.
Target Market(s)
ages 15-45
Colors
Designer to choose colors to be used in the design.
Look and feel

```html
<!DOCTYPE html>
<html lang="en">
<head>
<meta charset="utf-8">
<title>Sierra Lantern Roots Festival – 5th Annual Banner</title>
<link rel="stylesheet" href="https://fonts.googleapis.com/css2?family=Russo+One&display=swap">
<style>
  :root {
    --night: #0d1a45;
    --night-deep: #081235;
    --haze: #3a3f8a;
    --cloud-magenta: #d63fd6;
    --cloud-violet: #6a3fe0;
    --cloud-blue: #2f3fc0;
    --disc-magenta: #d83ee6;
    --disc-rose: #c72a68;
    --ring-white: #ffffff;
    --ring-pink: #f47aa8;
    --accent-pink: #f25aa0;
    --dot-orange: #e8832e;
    --line-blue: #2a9fd6;
    --mark-yellow: #fff200;
    --type-light: #fff6e8;
  }
  html, body {
    margin: 0;
    padding: 0;
    overflow: hidden;
    background: var(--night-deep);
  }
  .banner {
    position: relative;
    width: 1200px;
    height: 600px;
    overflow: hidden;
    background:
      radial-gradient(ellipse 420px 300px at 1050px 230px, rgba(120,110,200,0.35), transparent 70%),
      radial-gradient(ellipse 500px 260px at 700px 120px, rgba(60,70,150,0.35), transparent 70%),
      linear-gradient(180deg, var(--night) 0%, #13205a 60%, var(--night-deep) 100%);
    font-family: "Russo One", "Arial Black", sans-serif;
  }
  .cloud-bank {
    position: absolute;
    left: 260px;
    top: 300px;
    width: 1000px;
    height: 340px;
    border-radius: 50% 45% 0 0 / 60% 55% 0 0;
    background:
      radial-gradient(ellipse 260px 120px at 700px 110px, rgba(214,63,214,0.9), transparent 70%),
      radial-gradient(ellipse 300px 140px at 280px 150px, rgba(200,60,220,0.85), transparent 72%),
      radial-gradient(ellipse 360px 160px at 520px 230px, rgba(106,63,224,0.9), transparent 75%),
      linear-gradient(180deg, rgba(214,63,214,0.55) 0%, var(--cloud-violet) 55%, var(--cloud-blue) 100%);
    filter: blur(6px);
  }
  .decor {
    position: absolute;
    inset: 0;
    width: 1200px;
    height: 600px;
  }
  .eyebrow {
    position: absolute;
    left: 440px;
    top: 196px;
    margin: 0;
    font-size: 25px;
    letter-spacing: 0.5px;
    color: var(--type-light);
  }
  .rule {
    position: absolute;
    height: 6px;
    background: var(--line-blue);
  }
  .rule--top { left: 443px; top: 234px; width: 469px; }
  .rule--side { left: 287px; top: 349px; width: 94px; }
  .wordmark {
    position: absolute;
    left: 287px;
    top: 250px;
    width: 622px;
    margin: 0;
    color: var(--mark-yellow);
    font-weight: 400;
    line-height: 1;
  }
  .wordmark__line {
    display: block;
  }
  .wordmark__line--primary {
    font-size: 67px;
    letter-spacing: 1px;
    text-align: center;
  }
  .wordmark__line--secondary {
    margin-top: 12px;
    margin-left: 182px;
    font-size: 46px;
    letter-spacing: 1px;
  }
  .tagline {
    position: absolute;
    left: 477px;
    top: 412px;
    margin: 0;
    font-size: 21px;
    color: var(--type-light);
    letter-spacing: 0.3px;
  }
</style>
</head>
<body>
<main class="banner">
  <div class="cloud-bank" role="img" aria-label="Billowing magenta and violet smoke clouds across the lower half"></div>

  <svg class="decor" viewBox="0 0 1200 600" aria-hidden="true">
    <!-- soft dotted-disc areas rendered as flat tone -->
    <circle cx="381" cy="47" r="85" fill="none" stroke="var(--dot-orange)" stroke-width="60" opacity="0.45"/>
    <circle cx="82" cy="222" r="70" fill="var(--dot-orange)" opacity="0.35"/>

    <!-- large rose disc -->
    <circle cx="10" cy="390" r="180" fill="var(--disc-rose)" opacity="0.85"/>
    <!-- magenta disc with centre hole -->
    <circle cx="130" cy="247" r="74" fill="var(--disc-magenta)" opacity="0.92"/>
    <circle cx="130" cy="247" r="21" fill="var(--night)"/>

    <!-- rings -->
    <circle cx="187" cy="390" r="35" fill="none" stroke="var(--ring-white)" stroke-width="7"/>
    <circle cx="1180" cy="4" r="36" fill="none" stroke="var(--ring-white)" stroke-width="7"/>
    <circle cx="70" cy="595" r="34" fill="none" stroke="var(--ring-pink)" stroke-width="7"/>
    <circle cx="193" cy="510" r="20" fill="none" stroke="var(--ring-pink)" stroke-width="6" opacity="0.8"/>
    <circle cx="164" cy="562" r="24" fill="var(--accent-pink)"/>

    <!-- plus mark -->
    <path d="M1076 20v22M1065 31h22" stroke="var(--disc-magenta)" stroke-width="5" stroke-linecap="round"/>

    <!-- triangles -->
    <polygon points="1105,78 1131,94 1110,112" fill="var(--accent-pink)"/>
    <polygon points="1140,110 1166,126 1145,144" fill="var(--accent-pink)"/>
  </svg>

  <p class="eyebrow">5TH ANNUAL</p>
  <span class="rule rule--top"></span>

  <h1 class="wordmark">
    <span class="wordmark__line wordmark__line--primary">SIERRA LANTERN</span>
    <span class="wordmark__line wordmark__line--secondary">ROOTS FESTIVAL</span>
  </h1>
  <span class="rule rule--side"></span>

  <p class="tagline">MUSIC CONFERENCE &amp; CONCERT SERIES</p>
</main>
</body>
</html>
```